Business Card Design

New business card design

Target Market(s)

Residential & Commercial Property Managers

Industry/Entity Type

Plumbing Services

Contact Information for Business Card

Name - Rowan Keddle, title - Director, Phone Number - 0431 286 517, email - rowan@tbk-plumbing.com.au, Company ABN - 73 215 904 386,

Font styles to use
Sans Serif

Colors
0054AA
0677BA
7BADD7
CADEEF
E8F1F8

```html
<!DOCTYPE html>
<html lang="en">
<head>
<meta charset="utf-8">
<title>TBK Plumbing Services – Business Card</title>
<link rel="stylesheet" href="https://fonts.googleapis.com/css2?family=Montserrat:wght@400;500;700&display=swap">
<style>
  :root{
    --bg:#2a2c30;
    --card-dark:#1d232b;
    --card-dark-mark:#2e3540;
    --card-light:#ffffff;
    --ink:#1b232c;
    --blue:#29a3dc;
    --blue-deep:#0677ba;
  }
  *{margin:0;padding:0;box-sizing:border-box}
  html,body{width:1200px;height:880px;overflow:hidden}
  body{background:var(--bg);font-family:"Montserrat",sans-serif;position:relative}

  .card{position:absolute;width:580px;height:330px;border-radius:22px;box-shadow:0 14px 30px rgba(0,0,0,.45);overflow:hidden}
  .card--front{left:70px;top:70px;background:var(--card-dark)}
  .card--back{left:550px;top:480px;background:var(--card-light)}

  .brand{position:absolute;display:flex;align-items:center;gap:12px}
  .brand__dot{border-radius:50%;flex:none}
  .brand__name{font-weight:500;letter-spacing:.03em;line-height:1.2}

  .card--front .brand{left:0;right:0;top:0;bottom:0;justify-content:center}
  .card--front .brand__dot{width:20px;height:20px;background:var(--card-dark-mark)}
  .card--front .brand__name{font-size:32px;color:var(--card-dark-mark);white-space:nowrap}

  .card--back .brand{left:40px;top:130px;width:240px}
  .card--back .brand__dot{width:16px;height:16px;background:var(--blue)}
  .card--back .brand__name{font-size:24px;color:var(--ink);max-width:200px}

  .divider{position:absolute;left:300px;top:60px;width:2px;height:200px;background:var(--blue)}

  .contact{position:absolute;left:318px;top:66px;color:var(--ink);white-space:nowrap}
  .contact__name{font-weight:700;font-size:23px;color:var(--blue);line-height:1.1}
  .contact__title{font-size:15px;margin-top:4px}
  .contact__abn{font-size:13px;margin-top:18px}
  .contact__list{list-style:none;margin-top:22px;font-size:13.5px}
  .contact__list li{display:flex;align-items:center;gap:8px;margin-bottom:8px}
  .contact__icon{width:15px;height:15px;flex:none}
</style>
</head>
<body>
  <section class="card card--front" aria-label="Card front">
    <div class="brand">
      <span class="brand__dot"></span>
      <span class="brand__name">TBK Plumbing Services</span>
    </div>
  </section>

  <section class="card card--back" aria-label="Card back">
    <div class="brand">
      <span class="brand__dot"></span>
      <span class="brand__name">TBK Plumbing Services</span>
    </div>
    <div class="divider"></div>
    <div class="contact">
      <p class="contact__name">Rowan Keddle</p>
      <p class="contact__title">Director</p>
      <p class="contact__abn">Company ABN - 73 215 904 386</p>
      <ul class="contact__list">
        <li>
          <svg class="contact__icon" viewBox="0 0 24 24" aria-hidden="true"><path fill="#29a3dc" d="M6.6 10.8a15 15 0 0 0 6.6 6.6l2.2-2.2a1 1 0 0 1 1-.25 11.4 11.4 0 0 0 3.6.57 1 1 0 0 1 1 1V20a1 1 0 0 1-1 1A17 17 0 0 1 3 4a1 1 0 0 1 1-1h3.5a1 1 0 0 1 1 1c0 1.25.2 2.45.57 3.57a1 1 0 0 1-.25 1z"/></svg>
          <span>0431 286 517</span>
        </li>
        <li>
          <svg class="contact__icon" viewBox="0 0 24 24" aria-hidden="true"><rect x="2" y="5" width="20" height="14" rx="2" fill="#29a3dc"/><path d="M3 6l9 7 9-7" fill="none" stroke="#fff" stroke-width="1.6"/></svg>
          <span>rowan@tbk-plumbing.com.au</span>
        </li>
      </ul>
    </div>
  </section>
</body>
</html>
```